Meadowlight Soaps Business Card

The new business card design will incorporate my new logo components designed by one of your designers. Meadowlight Soaps creates high quality soaps and bath products. They would be suited for a Spa, Bed and Breakfast, Boutique environment. The look should be a white background.
Classy, soft and using the colour palet of the logo. The card will be two sided.

Reason: Need more time to make some changes and decide.

Target Market(s)

Looking to appeal to an upper end market. Spas, boutiques, independent gift stores, bridal salons, bed and breakfast, etc. I want the card to impart a sense of elegance, tranquility and Meadowlight. But also quality and value.

Industry/Entity Type

Business

Font styles to use
Sans Serif
Script

Requirements
Must have
• My logo on the front. But also on the back but faded out to allow written notes on the back.
On the front : Carol Pritchett
Owner/Creator
48 Fenwick Rd
Linden Falls, Ont N4K 2P9
519.402.6183
Creating Quality Handcrafted Soaps And Bath Products
Custom and Wholesale Orders Welcome
Www.meadowlightsoaps.ca
Www.facebook.com / MeadowlightSoapandBath
info@meadowlightsoaps.ca

```html
<!DOCTYPE html>
<html lang="en">
<head>
<meta charset="utf-8">
<title>Meadowlight Soaps – Business Card</title>
<link href="https://fonts.googleapis.com/css2?family=Great+Vibes&family=Roboto:wght@300;400&display=swap" rel="stylesheet">
<style>
  :root {
    --canvas: #ecebe8;
    --card: #ffffff;
    --teal: #8fbfb5;
    --teal-soft: #c8e0da;
    --teal-faint: #edf4f2;
    --ink: #3d3d3d;
    --ink-soft: #6b6b6b;
    --rule: #cfcfcf;
    --band: #3a3a3a;
    --cream-1: #f6f3e6;
    --cream-2: #e9e2c8;
    --cream-3: #d9cfae;
    --cocoa: #6b4a35;
  }
  * { margin: 0; padding: 0; box-sizing: border-box; }
  html, body { width: 1200px; height: 858px; overflow: hidden; background: var(--canvas); }
  body { position: relative; font-family: "Roboto", Arial, sans-serif; font-weight: 300; color: var(--ink); }

  .card {
    position: absolute; top: 269px; width: 560px; height: 320px;
    background: var(--card); box-shadow: 0 6px 18px rgba(0,0,0,.18); overflow: hidden;
  }
  .card--front { left: 20px; }
  .card--back { left: 620px; }

  /* Front */
  .brand { position: absolute; left: 28px; top: 36px; display: flex; align-items: center; gap: 10px; }
  .brand__name { font-size: 26px; font-weight: 300; letter-spacing: 1px; color: var(--teal); line-height: 1; }
  .brand__dot { width: 12px; height: 12px; border-radius: 50%; background: var(--teal-soft); }

  .holder { position: absolute; right: 28px; top: 22px; text-align: right; }
  .holder__name { font-family: "Great Vibes", cursive; font-size: 30px; color: var(--teal); line-height: 1.1; }
  .holder__role { font-size: 13px; color: var(--ink-soft); margin-top: 2px; }

  .product-band {
    position: absolute; left: 0; right: 0; top: 96px; height: 140px;
    border-top: 3px solid var(--teal-soft); border-bottom: 3px solid var(--teal-soft);
    background: linear-gradient(90deg, var(--cream-1) 0%, var(--cream-2) 45%, var(--cream-3) 80%, var(--cocoa) 100%);
  }

  .contact { position: absolute; left: 28px; bottom: 22px; font-size: 14px; line-height: 22px; }
  .address { position: absolute; right: 28px; bottom: 22px; font-size: 14px; line-height: 22px; }
  .row { display: flex; align-items: center; gap: 8px; }
  .row svg { flex: none; }
  .row--indent { padding-left: 18px; }

  /* Back */
  .back__mark {
    position: absolute; left: 0; right: 0; top: 118px; text-align: center; z-index: 0;
    font-size: 44px; font-weight: 300; letter-spacing: 2px; color: var(--teal-faint); line-height: 1;
  }
  .note-title {
    position: absolute; right: 44px; top: 16px; z-index: 1;
    font-family: "Great Vibes", cursive; font-size: 40px; color: var(--teal); line-height: 1.2;
  }
  .note-lines { position: absolute; left: 40px; right: 40px; top: 78px; z-index: 1; }
  .note-lines span { display: block; height: 30px; border-bottom: 1px solid var(--rule); }
  .web { position: absolute; left: 40px; bottom: 70px; font-size: 12px; color: var(--ink-soft); z-index: 1; }
  .web i { font-style: normal; margin: 0 8px; }
  .tagline {
    position: absolute; left: 0; right: 0; bottom: 14px; height: 48px; background: var(--band);
    color: #fff; font-size: 13px; line-height: 20px; padding: 4px 40px; font-weight: 400; z-index: 1;
  }
</style>
</head>
<body>

<section class="card card--front">
  <div class="brand">
    <span class="brand__name">Meadowlight Soaps</span>
    <span class="brand__dot"></span>
  </div>
  <div class="holder">
    <div class="holder__name">Carol Pritchett</div>
    <div class="holder__role">Owner</div>
  </div>

  <div class="product-band" role="img" aria-label="Photograph of a row of handcrafted soap bars"></div>

  <div class="contact">
    <div class="row">
      <svg width="12" height="12" viewBox="0 0 24 24"><path fill="#555" d="M6.6 10.8a15 15 0 0 0 6.6 6.6l2.2-2.2c.3-.3.7-.4 1-.2 1.1.4 2.3.6 3.6.6.6 0 1 .4 1 1V20c0 .6-.4 1-1 1A17 17 0 0 1 3 4c0-.6.4-1 1-1h3.5c.6 0 1 .4 1 1 0 1.3.2 2.5.6 3.6.1.3 0 .7-.2 1z"/></svg>
      <span>705.402.6183</span>
    </div>
    <div class="row">
      <svg width="12" height="10" viewBox="0 0 24 18"><rect x="1" y="1" width="22" height="16" fill="none" stroke="#555" stroke-width="2"/><path d="M1 1l11 9 11-9" fill="none" stroke="#555" stroke-width="2"/></svg>
      <span>info@meadowlightsoaps.ca</span>
    </div>
  </div>

  <div class="address">
    <div class="row">
      <svg width="10" height="13" viewBox="0 0 20 26"><path fill="#555" d="M10 0a9 9 0 0 0-9 9c0 7 9 17 9 17s9-10 9-17a9 9 0 0 0-9-9zm0 12a3 3 0 1 1 0-6 3 3 0 0 1 0 6z"/></svg>
      <span>48 Fenwick Rd</span>
    </div>
    <div class="row--indent">Linden Falls, Ont N4K 2P9</div>
  </div>
</section>

<section class="card card--back">
  <div class="back__mark" aria-hidden="true">Meadowlight Soaps</div>
  <div class="note-title">Note</div>
  <div class="note-lines"><span></span><span></span><span></span><span></span></div>
  <div class="web">www.meadowlightsoaps.ca<i>|</i>www.facebook.com/MeadowlightSoapandBath</div>
  <div class="tagline">
    Creating Quality Handcrafted Soaps And Bath Products<br>
    Custom &amp; Wholesale Orders Welcome
  </div>
</section>

</body>
</html>
```